Start up Dialysis Clinic needs its first website - Velmira Health

Create a visually appealing and user-friendly website for Velmira Health, a dialysis clinic located in Mt. Irvine, Tobago. The website should effectively communicate our services to local, regional, and international patients, providing essential information and fostering trust and engagement..
Key Goals:

1. Informative: Provide comprehensive information about our services, facility, and team.
2. User-Friendly: Ensure the website is easy to navigate, with a clear structure and accessible content.
3. Engaging: Create a visually appealing design that reflects the professionalism and care of Velmira Health.
4. Responsive: Ensure the website is fully responsive and performs well on all devices, including desktops, tablets, and smartphones.
5. Trust-Building: Include testimonials, credentials, and patient resources to build trust with potential patients.
Scope of Work:

1. Home Page: An inviting and informative landing page that provides an overview of our clinic, mission, and services. Include a call to action for more information and contact details.
2. About Us: A detailed page about Velmira Health, including our mission, vision, team, and facility tour.
3. Services: A comprehensive page describing the dialysis services we offer, including Hemodialysis, Peritoneal Dialysis, and Home Hemodialysis.
4. Patient Information: A resourceful section with guides for new patients, FAQs, insurance and billing information, and downloadable forms.
5. Resources: Educational content about kidney health, dialysis options, diet and nutrition tips, and support groups.
6. Contact Us: A contact page with our address, phone number, email, office hours, a contact form, and a map.

```html
<!DOCTYPE html>
<html lang="en">
<head>
<meta charset="utf-8">
<title>Velmira Health — Dialysis Clinic</title>
<link href="https://fonts.googleapis.com/css2?family=Exo+2:wght@600;700&family=Roboto:wght@400;500;700&display=swap" rel="stylesheet">
<style>
:root{
  --blue:#2d7dc2;
  --green:#4a9461;
  --teal:#3a7f95;
  --dark:#222;
  --text:#555;
  --white:#fff;
}
*{box-sizing:border-box;margin:0;padding:0}
html,body{width:1200px;height:3894px;overflow:hidden}
body{position:relative;font-family:'Roboto',sans-serif;color:var(--text);background:#fff}
.abs{position:absolute}
.heading{font-family:'Exo 2',sans-serif;font-weight:700;text-transform:uppercase;letter-spacing:1px}
.btn{position:absolute;background:var(--green);color:#fff;font-weight:700;font-size:14px;display:flex;align-items:center;justify-content:center;text-transform:uppercase;letter-spacing:.5px}
.mark{display:inline-block;width:18px;height:18px;background:var(--green);vertical-align:middle}
.divider{display:flex;align-items:center;gap:8px}
.divider .line{display:block;width:46px;height:3px;background:currentColor}
.divider .mark{width:18px;height:18px}
.photo{position:absolute}

/* header */
.topbar{left:372px;top:0;width:828px;height:60px;background:var(--blue);clip-path:polygon(0 0,100% 0,100% 100%,9% 100%);color:#fff;font-size:18px}
.topbar .item{position:absolute;top:12px;display:flex;align-items:center;gap:12px}
.ico{width:36px;height:36px;border-radius:50%;background:#fff;display:flex;align-items:center;justify-content:center}
.navbar{left:362px;top:60px;width:838px;height:65px;background:var(--green);clip-path:polygon(5% 0,100% 0,100% 100%,0 100%);display:flex;align-items:center;padding-left:65px}
.navbar a{color:#fff;text-decoration:none;font-size:14px;font-weight:500;padding:0 16px;border-right:1px solid rgba(255,255,255,.5)}
.navbar a:last-child{border:none}
.brand{left:112px;top:18px;display:flex;align-items:center;gap:10px}
.brand span{font-family:'Exo 2',sans-serif;font-weight:700;font-size:30px;color:var(--blue);text-transform:uppercase}

/* service cards */
.svc{position:absolute;top:1628px;width:301px;height:374px;background:#fff;border-radius:4px;overflow:hidden;text-align:center}
.svc .img{height:208px}
.svc h3{font-size:16px;font-weight:500;color:var(--dark);margin-top:24px;text-transform:uppercase}
.svc p{font-size:14.5px;line-height:25px;margin:12px 20px 0}
.svc .more{font-size:14px;font-weight:700;color:var(--green);margin-top:8px;display:flex;justify-content:center;align-items:center;gap:6px}
.svc .more b{width:18px;height:18px;border-radius:50%;background:var(--green);display:inline-block}

/* reviews */
.review{position:absolute;top:2420px;height:346px;background:#fff;box-shadow:0 2px 10px rgba(0,0,0,.15);padding:40px 30px}
.review .name{font-size:25px;color:var(--dark)}
.review .date{font-size:15px;color:#999;margin-top:4px}
.review .stars{color:#f5b400;font-size:21px;letter-spacing:2px;margin-top:8px}
.review p{font-size:15px;line-height:26px;margin-top:10px}
.review .rm{font-size:15px;font-weight:700;color:var(--green);text-decoration:underline;margin-top:22px;display:block}
.review .dot{position:absolute;right:40px;top:40px;width:46px;height:46px;border-radius:50%;border:5px solid #dde3e8}
.review.active{background:var(--blue)}
.review.active .name,.review.active p,.review.active .rm{color:#fff}
.review.active .date{color:#dbe7f5}

.field{position:absolute;left:111px;width:444px;height:54px;background:#fff;border:1px solid #ccc;padding:18px 8px;font-size:14px;color:#888}

/* footer */
.footer{left:0;top:3506px;width:1200px;height:388px;background:var(--blue);color:#fff}
.footer-title{position:absolute;font-family:'Exo 2',sans-serif;font-size:20px;font-weight:600;color:#fff;text-transform:uppercase}
.contact-row{position:absolute;left:676px;display:flex;align-items:center;gap:12px;font-size:15px;font-weight:500;line-height:22px;color:#fff}
.contact-row .ico{width:48px;height:48px;border:3px solid #fff;background:transparent}
.social{position:absolute;top:3625px;width:34px;height:34px;border-radius:50%;background:#fff}
</style>
</head>
<body>

<!-- header -->
<div class="abs brand"><i class="mark" style="width:34px;height:34px"></i><span>Velmira Health</span></div>
<div class="abs topbar">
  <div class="item" style="left:185px"><span class="ico"><svg width="18" height="18" viewBox="0 0 24 24"><path fill="#2d7dc2" d="M6.6 10.8a15 15 0 006.6 6.6l2.2-2.2c.3-.3.7-.4 1-.2 1.1.4 2.3.6 3.6.6.6 0 1 .4 1 1V20c0 .6-.4 1-1 1A17 17 0 013 4c0-.6.4-1 1-1h3.5c.6 0 1 .4 1 1 0 1.3.2 2.5.6 3.6.1.3 0 .7-.2 1z"/></svg></span>+1 (868) 555 0142</div>
  <div class="item" style="left:448px"><span class="ico"><svg width="18" height="18" viewBox="0 0 24 24"><path fill="#2d7dc2" d="M3 5h18v14H3z"/><path fill="none" stroke="#fff" stroke-width="2" d="M3 6l9 7 9-7"/></svg></span>info@velmirahealth.com</div>
</div>
<nav class="abs navbar">
  <a>HOME</a><a>ABOUT US</a><a>SERVICES</a><a>PATIENT INFORMATION</a><a>RESOURCES</a><a>CONTACT</a>
</nav>

<!-- hero -->
<div class="abs" style="left:0;top:133px;width:1200px;height:727px;background:linear-gradient(90deg,#f6f9fd 0%,#eaf1fa 45%,#dae7f4 100%)"></div>
<div class="photo" role="img" aria-label="Photo of a smiling nurse in blue scrubs with a stethoscope" style="left:585px;top:133px;width:615px;height:680px;background:linear-gradient(135deg,#e3edf7 0%,#c4d8ec 55%,#a7c4e2 100%)"></div>
<svg class="abs" style="left:0;top:620px" width="1200" height="240" viewBox="0 0 1200 240">
  <polygon points="0,40 600,215 1200,40 1200,240 0,240" fill="#fff"/>
  <polygon points="45,60 600,237 1200,45 1200,80 600,200 45,58" fill="var(--teal)"/>
</svg>
<div class="abs heading" style="left:111px;top:264px;font-size:24px;color:var(--green)">Velmira Health</div>
<h1 class="abs heading" style="left:111px;top:300px;font-size:63px;line-height:72px;color:var(--blue)">Take care of<br>your health</h1>
<p class="abs" style="left:111px;top:455px;width:480px;font-size:15px;line-height:24px">Lorem ipsum dolor sit amet, consectetur adipiscing elit, usmod por incididunt ut labore et dolore magna aliqua. Quis ipsum suspendisse ultrices gravida.</p>
<div class="btn" style="left:111px;top:542px;width:152px;height:51px">Get Started</div>

<!-- about -->
<div class="photo" role="img" aria-label="Photo of a male and a female doctor in white coats" style="left:90px;top:940px;width:530px;height:492px;background:linear-gradient(180deg,#f3f3f3 0%,#e6e6e6 60%,#d9dde2 100%)"></div>
<h2 class="abs heading" style="left:645px;top:940px;font-size:42px;color:var(--blue)">About <span style="color:var(--green)">Us</span></h2>
<div class="abs divider" style="left:645px;top:998px;color:var(--blue)"><i class="mark"></i><i class="line"></i></div>
<div class="abs" style="left:645px;top:1052px;width:445px;font-size:14.5px;line-height:28.5px;text-align:justify">
  <p>Lorem ipsum dolor sit amet, consectetur adipiscing elit, sed do eiusmod tempor incididunt ut labore et dolore magna aliqua. uis ipsum suspendisse ultrices gravida. Risus commodo velcilisis. Lorem ipsum dolor sit amet, consectetur adipiscing elit, sed do eiusmod tempor incididunt ut labore et dolore magna aliqua.</p>
  <p style="margin-top:8px">Lorem ipsum dolor sit amet, consectetur adipiscing elit, sed do eiusmod tempor incididunt ut labore et dolore magna aliqua.</p>
</div>
<div class="btn" style="left:645px;top:1280px;width:151px;height:51px">Read More</div>

<!-- services -->
<div class="abs" style="left:0;top:1432px;width:1200px;height:676px;background:linear-gradient(120deg,#3a7f95 0%,#3a7f95 45%,#3f8693 60%,#4a9461 100%)"></div>
<svg class="abs" style="left:0;top:1432px" width="1200" height="676"><polygon points="320,0 1200,0 1200,330" fill="#fff" opacity=".06"/></svg>
<h2 class="abs heading" style="left:0;top:1490px;width:1200px;text-align:center;font-size:42px;color:#fff">Our Services</h2>
<div class="abs divider" style="left:536px;top:1558px;color:#fff"><i class="line"></i><i class="mark" style="background:#fff"></i><i class="line"></i></div>
<div class="svc" style="left:111px"><div class="img" role="img" aria-label="Photo of a patient receiving hemodialysis" style="background:linear-gradient(180deg,#d7e6f2,#9fbbd3)"></div><h3>Including Hemodialysis</h3><p>Lorem ipsum dolor sit ametsectetur adipiscing elit,ultrices gravida.</p><div class="more">READ MORE <b></b></div></div>
<div class="svc" style="left:450px;border-bottom:5px solid var(--green)"><div class="img" role="img" aria-label="Photo of hands holding a kidney model" style="background:linear-gradient(180deg,#d9dade,#b5b8bf)"></div><h3 style="color:var(--green)">Peritoneal Dialysis</h3><p>Lorem ipsum dolor sit ametsectetur adipiscing elit,ultrices gravida.</p><div class="more">READ MORE <b></b></div></div>
<div class="svc" style="left:788px"><div class="img" role="img" aria-label="Photo of a care team beside a dialysis machine" style="background:linear-gradient(180deg,#eceae4,#c7ccd0)"></div><h3>Home Hemodialysis</h3><p>Lorem ipsum dolor sit ametsectetur adipiscing elit,ultrices gravida.</p><div class="more">READ MORE <b></b></div></div>
<svg class="abs" style="left:574px;top:2028px" width="52" height="16"><circle cx="8" cy="8" r="5" fill="none" stroke="#fff"/><circle cx="26" cy="8" r="6" fill="#fff"/><circle cx="44" cy="8" r="5" fill="none" stroke="#fff"/></svg>

<!-- testimonials -->
<div class="photo" role="img" aria-label="Photo of a patient talking with a doctor by a window" style="left:656px;top:2108px;width:544px;height:312px;background:linear-gradient(90deg,#e4e8ec 0%,#cfd6de 60%,#b3bfcc 100%)"></div>
<h2 class="abs heading" style="left:111px;top:2212px;font-size:42px;color:var(--blue)">Client <span style="color:var(--green)">Testimonials</span></h2>
<div class="abs divider" style="left:265px;top:2287px;color:var(--blue)"><i class="line"></i><i class="mark"></i><i class="line"></i></div>
<svg class="abs" style="left:278px;top:2338px" width="116" height="44">
  <circle cx="22" cy="22" r="21" fill="#2d7dc2"/><path d="M25 14l-8 8 8 8" stroke="#fff" stroke-width="2.5" fill="none"/>
  <circle cx="93" cy="22" r="20" fill="#fff" stroke="#333" stroke-width="1.5"/><path d="M90 14l8 8-8 8" stroke="#333" stroke-width="2" fill="none"/>
</svg>
<div class="review" style="left:132px;width:345px"><span class="dot"></span><div class="name">Marisol</div><div class="date">5 February 2024</div><div class="stars">★★★★★</div><p>Lorem ipsum dolor sit et,ctetur ipiscing elit, sed do mpor unt ut labore et dolore magna liqua. Quis Lorem ipsum dolor sit et,ctetur ipiscing elit, sed Lorem ipsum dolor sit et,ctetur ipiscing elit</p><span class="rm">READ MORE</span></div>
<div class="review active" style="left:500px;width:345px"><span class="dot" style="border-color:#fff"></span><div class="name">Dorian</div><div class="date">19 February 2024</div><div class="stars">★★★★★</div><p>Lorem ipsum dolor sit et,ctetur ipiscing elit, sed do mpor unt ut labore et dolore magna liqua. Quis Lorem ipsum dolor sit et,ctetur ipiscing elit, sed Lorem ipsum dolor sit et,ctetur ipiscing elit</p><span class="rm">READ MORE</span></div>
<div class="review" style="left:869px;width:331px;padding-right:20px"><span class="dot"></span><div class="name">Keaton</div><div class="date">24 May 2024</div><div class="stars">★★★★★</div><p>Lorem ipsum dolor sit et,ctetur ipiscing elit, sed do mpor unt ut labore et dolore magna liqua. Quis Lorem ipsum dolor sit et,ctetur ipiscing elit, sed Lorem ipsum dolor sit et,ctetur ipiscing elit</p><span class="rm">READ MORE</span></div>

<!-- contact -->
<div class="abs" style="left:0;top:2866px;width:1200px;height:640px;background:linear-gradient(120deg,#4a9461 0%,#3f8a82 25%,#3a7f95 55%,#2f6e86 100%)"></div>
<div class="photo" role="img" aria-label="Photo of a smiling doctor with glasses holding a tablet" style="left:625px;top:2866px;width:575px;height:640px;background:linear-gradient(160deg,#5a8ea2 0%,#6f9db0 50%,#4f7f93 100%);clip-path:polygon(12% 0,100% 0,100% 100%,0 100%)"></div>
<h2 class="abs heading" style="left:111px;top:2935px;font-size:40px;color:#fff">Get in Touch</h2>
<div class="abs divider" style="left:122px;top:2988px;color:#fff"><i class="line"></i><i class="mark" style="background:#fff"></i><i class="line"></i></div>
<div class="field" style="top:3061px">Name</div>
<div class="field" style="top:3131px">Email</div>
<div class="field" style="top:3203px">Phone Number</div>
<div class="field" style="top:3275px;height:100px;padding-top:12px">Message...</div>
<div class="btn" style="left:111px;top:3392px;width:152px;height:51px;background:#fff;color:#111">Submit</div>

<!-- footer -->
<footer class="abs footer"></footer>
<div class="abs" style="left:98px;top:3578px;width:262px;display:flex;flex-direction:column;align-items:center;gap:14px">
  <i class="mark" style="width:70px;height:70px;background:#fff"></i>
  <span style="font-family:'Exo 2',sans-serif;font-weight:700;font-size:30px;text-transform:uppercase;color:#fff;white-space:nowrap">Velmira Health</span>
</div>
<div class="footer-title" style="left:443px;top:3575px">Quick Links</div>
<div class="abs" style="left:446px;top:3618px;font-size:15px;font-weight:500;line-height:34.5px;color:#fff">Home<br>About Us<br>Services<br>Patient Information<br>Resources<br>Contact</div>
<div class="footer-title" style="left:676px;top:3575px">Contact Us</div>
<div class="contact-row" style="top:3630px"><span class="ico"><svg width="20" height="20" viewBox="0 0 24 24"><path fill="#fff" d="M6.6 10.8a15 15 0 006.6 6.6l2.2-2.2c.3-.3.7-.4 1-.2 1.1.4 2.3.6 3.6.6.6 0 1 .4 1 1V20c0 .6-.4 1-1 1A17 17 0 013 4c0-.6.4-1 1-1h3.5c.6 0 1 .4 1 1 0 1.3.2 2.5.6 3.6.1.3 0 .7-.2 1z"/></svg></span><div>Phone No:<br>+1 (868) 555 0142</div></div>
<div class="contact-row" style="top:3705px"><span class="ico"><svg width="20" height="20" viewBox="0 0 24 24"><path fill="#fff" d="M12 2a7 7 0 00-7 7c0 5 7 13 7 13s7-8 7-13a7 7 0 00-7-7zm0 9.5A2.5 2.5 0 1112 6a2.5 2.5 0 010 5.5z"/></svg></span><div>Location:<br>Mt. Irvine, Tobago</div></div>
<div class="contact-row" style="top:3780px"><span class="ico"><svg width="20" height="20" viewBox="0 0 24 24"><path fill="#fff" d="M3 5h18v14H3z"/><path fill="none" stroke="#2d7dc2" stroke-width="2" d="M3 6l9 7 9-7"/></svg></span><div>Email:<br>info@velmirahealth.com</div></div>
<div class="footer-title" style="left:956px;top:3570px">Follow Up</div>
<span class="social" style="left:956px"></span>
<span class="social" style="left:1000px"></span>
<span class="social" style="left:1043px"></span>
<div class="abs" style="left:0;top:3852px;width:1200px;text-align:center;font-size:15px;color:#fff">Copyright © 2024 Velmira Health | All Rights Reserved</div>

</body>
</html>
```